Cedarvale Ridge College

We are looking to update our current webpage at www.cedarvaleridge.ca. We would like to make it modern, fresh and appealing to students. We want to keep our logo the same with the logo colours blended in as the primary colours and focus. We are open to reconfiguring content as well.
Reason: Hi, In the next 3 days we will have narrowed our search to 3 designs and will make a choice before the final deadline...
College

```html
<!DOCTYPE html>
<html lang="en">
<head>
<meta charset="utf-8">
<title>Cedarvale Ridge College</title>
<link href="https://fonts.googleapis.com/css2?family=Arimo:ital,wght@0,400;0,700;1,400&family=Source+Sans+3:wght@400;600;700&display=swap" rel="stylesheet">
<style>
:root{
  --navy:#0f2147;
  --navy-footer:#0e2248;
  --navy-bar:#1a3264;
  --tile-1:#13295a;
  --tile-2:#1a3468;
  --tile-3:#1d3a76;
  --tile-4:#22458a;
  --link:#13306e;
  --text:#6a6a6a;
  --heading:#2b2b2b;
  --rule:#cfcfcf;
  --white:#ffffff;
  --social:#d2d2d2;
  --footer-text:#e6eaf2;
  --footer-muted:#5d77b0;
}
*{margin:0;padding:0;box-sizing:border-box}
html,body{width:708px;height:1200px;overflow:hidden;background:var(--white)}
body{position:relative;font-family:"Arimo",Arial,sans-serif;color:var(--text)}
.abs{position:absolute}

.hero-photo{left:0;top:0;width:708px;height:523px;background:linear-gradient(100deg,#8a8278 0%,#c9c3bb 30%,#e9e6e2 55%,#d8d4d0 75%,#f2f1ef 100%)}

.topbar{left:83px;top:0;width:542px;height:21px;background:var(--navy);color:var(--white);font-size:7px;display:flex;align-items:center;padding:0 19px;white-space:nowrap}
.topbar .links{flex:1}
.topbar .contact{display:flex;gap:16px;align-items:center}
.topbar .contact span{display:flex;align-items:center;gap:5px}

.header{left:83px;top:21px;width:542px;height:70px;background:var(--white)}
.brand{position:absolute;left:12px;top:27px;display:flex;align-items:center;gap:7px}
.brand-mark{width:13px;height:13px;border-radius:50%;background:var(--link)}
.brand-name{font-family:"Source Sans 3",sans-serif;font-weight:700;font-size:17px;color:var(--link);line-height:1;white-space:nowrap}
.social{position:absolute;right:15px;top:28px;display:flex;gap:3px}
.social span{width:17px;height:17px;border-radius:50%;background:var(--social)}

.nav{left:83px;top:91px;width:542px;height:36px;background:var(--white);display:flex;font-size:7.5px;border-top:1px solid #eee}
.nav a{flex:auto;display:flex;align-items:center;justify-content:center;padding:0 6px;border-right:1px solid #e6e6e6;text-decoration:none;color:#222;height:100%;white-space:nowrap}
.nav a.active{border-top:2px solid var(--navy)}
.nav a:last-child{border-right:none}

.slide-arrow{top:238px;width:23px;height:48px;background:var(--white);display:flex;align-items:center;justify-content:center}
.slide-arrow.prev{left:0;border-right:2px solid var(--navy)}
.slide-arrow.next{right:0;border-left:2px solid var(--navy)}

.caption{left:85px;background:rgba(23,40,82,.88);color:var(--white);font-size:11.5px;letter-spacing:.2px;padding:0 14px;height:33px;display:flex;align-items:center;white-space:nowrap}

.tiles{left:83px;top:478px;width:542px;height:94px;display:flex}
.tile{flex:1;display:flex;flex-direction:column;align-items:center;color:var(--white);font-size:9px;padding-top:13px;white-space:nowrap}
.tile .icon{width:46px;height:46px;border-radius:50%;background:var(--white);display:flex;align-items:center;justify-content:center;margin-bottom:10px}
.tile:nth-child(1){background:var(--tile-1)}
.tile:nth-child(2){background:var(--tile-2)}
.tile:nth-child(3){background:var(--tile-3)}
.tile:nth-child(4){background:var(--tile-4)}

.section-title{font-size:11px;font-weight:400;color:var(--heading);text-transform:uppercase;padding-bottom:6px;border-bottom:1px dotted var(--rule);white-space:nowrap}
.welcome-title{left:83px;top:594px;width:542px}
.welcome-photo{left:83px;top:626px;width:116px;height:85px;background:linear-gradient(135deg,#3b2a22,#6b4b3a 60%,#2a2422)}
.welcome-text{left:218px;top:627px;width:407px;font-size:6.4px;line-height:13.3px}
.welcome-text .lead{color:var(--link);font-style:italic;font-size:6.6px}
.btn-more{left:217px;top:696px;width:42px;height:18px;background:var(--navy);color:var(--white);font-size:6.5px;display:flex;align-items:center;justify-content:center}

.videos-title{left:83px;top:732px;width:224px}
.news-title{left:334px;top:732px;width:291px}
.video{left:83px;top:771px;width:214px;height:119px;background:linear-gradient(180deg,#1a1a1a 0 8px,#c9c3bc 8px,#9a8d82 95px,#1a1a1a 95px)}
.video .play{position:absolute;left:93px;top:44px;width:22px;height:20px;background:rgba(0,0,0,.8);border-radius:3px;display:flex;align-items:center;justify-content:center}
.video .progress{position:absolute;left:0;bottom:10px;width:214px;height:2px;background:#555}
.video .progress i{display:block;width:46px;height:2px;background:#d3222a}
.video-text{left:83px;top:900px;width:214px;font-size:6.5px;line-height:11px;text-align:justify}

.news-item{left:334px;width:291px;display:flex;gap:10px}
.news-thumb{width:68px;height:50px;border:2px solid #eee;flex:none}
.news-body h3{font-size:7.4px;color:var(--link);font-weight:400;margin-top:1px}
.news-body .date{font-size:6.2px;color:#a8a8a8;font-style:italic;margin:3px 0 2px}
.news-body p{font-size:6.2px;line-height:11px}

.footer{left:0;top:974px;width:708px;height:226px;background:var(--navy-footer);font-family:"Source Sans 3",sans-serif;color:var(--footer-text);font-size:6.8px}
.footer h4{font-size:9.5px;color:var(--white);font-weight:700;margin-bottom:11px}
.fcol{position:absolute;top:17px}
.fcol p{line-height:13px}
.fcol ul{list-style:none}
.fcol li{display:flex;gap:8px;line-height:16.6px;white-space:nowrap}
.fcol li::before{content:"";width:0;height:0;border-left:3px solid var(--footer-text);border-top:2.5px solid transparent;border-bottom:2.5px solid transparent;margin-top:5.5px}
.fcontact{margin-top:12px}
.fcontact div{display:flex;gap:7px;line-height:13px}
.tweet{display:flex;gap:7px;line-height:13px;margin-bottom:14px}
.tweet .dot{width:5px;height:5px;border-radius:50%;background:var(--footer-text);flex:none;margin-top:4px}
.tweet .muted{color:var(--footer-muted)}
.divider{position:absolute;top:17px;width:1px;height:155px;background:#1d356a}
.copyright{position:absolute;left:70px;top:182px;width:542px;height:44px;background:var(--navy-bar);display:flex;align-items:center;justify-content:space-between;padding:0 23px;font-family:"Arimo",sans-serif;font-size:6.5px;color:var(--white)}
</style>
</head>
<body>

<div class="abs hero-photo" role="img" aria-label="Photo of students seated in a classroom taking notes"></div>

<div class="abs topbar">
  <div class="links">Map &amp; Directions &nbsp;/&nbsp; Campus Map &nbsp;/&nbsp; Photo Tour</div>
  <div class="contact">
    <span><svg width="7" height="7" viewBox="0 0 10 10"><path d="M2 0l2 2.5-1 1.2c.6 1.4 1.8 2.6 3.2 3.2l1.2-1L10 8l-1.5 2C4 9.5.5 6 0 1.5z" fill="#fff"/></svg>(604) 555-0182</span>
    <span><svg width="8" height="6" viewBox="0 0 10 7"><rect width="10" height="7" fill="#fff"/><path d="M0 0l5 4 5-4" stroke="#0f2147" fill="none"/></svg>info@cedarvaleridge.ca</span>
  </div>
</div>

<header class="abs header">
  <div class="brand"><span class="brand-mark"></span><span class="brand-name">Cedarvale Ridge College</span></div>
  <div class="social"><span></span><span></span><span></span><span></span></div>
</header>

<nav class="abs nav">
  <a class="active">Home</a><a>About Us</a><a>Contact Us</a><a>Consider Cedarvale</a><a>Current Students</a><a>Alumni</a><a>Supporters</a><a>News + Events</a><a>Cedarvale Park</a>
</nav>

<div class="abs slide-arrow prev"><svg width="7" height="11" viewBox="0 0 7 11"><path d="M6 1L1.5 5.5 6 10" stroke="#0f2147" stroke-width="1.4" fill="none"/></svg></div>
<div class="abs slide-arrow next"><svg width="7" height="11" viewBox="0 0 7 11"><path d="M1 1l4.5 4.5L1 10" stroke="#0f2147" stroke-width="1.4" fill="none"/></svg></div>

<div class="abs caption" style="top:228px">LOREM IPSUM DOLOR SIT AMET CONSECTE</div>
<div class="abs caption" style="top:262px">ADIPISCING ELIT AENEAN COMMO</div>

<div class="abs tiles">
  <div class="tile"><div class="icon"><svg width="20" height="22" viewBox="0 0 20 22"><rect x="2" y="3" width="13" height="17" rx="1" fill="#13295a"/><rect x="5" y="1" width="7" height="4" rx="1" fill="#13295a" stroke="#fff"/><path d="M5 9h7M5 12h7M5 15h4" stroke="#fff"/><circle cx="15" cy="17" r="4" fill="#13295a" stroke="#fff"/><path d="M13 17l1.5 1.5L17 16" stroke="#fff" fill="none"/></svg></div>APPLY TODAY</div>
  <div class="tile"><div class="icon"><svg width="24" height="22" viewBox="0 0 24 22"><text x="10" y="11" font-size="12" font-family="Arimo" font-weight="700" fill="#1a3468">$</text><path d="M1 15h6l5 2h6l4-3v3l-5 4H8l-7-2z" fill="#1a3468"/></svg></div>DONATE</div>
  <div class="tile"><div class="icon"><svg width="24" height="18" viewBox="0 0 24 18"><path d="M12 4C9 2 5 2 2 3v13c3-1 7-1 10 1 3-2 7-2 10-1V3c-3-1-7-1-10 1z" fill="none" stroke="#1d3a76" stroke-width="2"/><path d="M12 4v13" stroke="#1d3a76" stroke-width="1.5"/></svg></div>LIBRARY</div>
  <div class="tile"><div class="icon"><svg width="18" height="22" viewBox="0 0 18 22"><rect x="2" y="2" width="14" height="18" rx="1" fill="none" stroke="#22458a" stroke-width="2"/><path d="M5 7h8M5 10h8M5 13h8M5 16h5" stroke="#22458a"/></svg></div>TEXT FOR INFO</div>
</div>

<h2 class="abs section-title welcome-title">Welcome to Cedarvale Ridge College</h2>
<div class="abs welcome-photo" role="img" aria-label="Photo of the college president speaking"></div>
<div class="abs welcome-text">
  <div class="lead">Thank-you for your interest in Cedarvale Ridge College!</div>
  <p>I hope that your visit here will answer some of your questions as you consider a course of study that is right for you. Whether you are interested in pastoral ministry, counselling, missions and cross-cultural communication, theology, worship arts, music or our one-year Omega program you'll discover we've designed programs that will equip you to excel in your chosen calling. Two of our newest programs are Not For Profit Organizational Leadership, and Sound Production, Music &amp; Media.For those of you that are looking to transition ...</p>
</div>
<div class="abs btn-more">More</div>

<h2 class="abs section-title videos-title">Latest Videos</h2>
<h2 class="abs section-title news-title">News &amp; Events</h2>

<div class="abs video" role="img" aria-label="Video still of a lecturer teaching a class">
  <div class="play"><svg width="7" height="8" viewBox="0 0 7 8"><path d="M0 0l7 4-7 4z" fill="#fff"/></svg></div>
  <div class="progress"><i></i></div>
</div>
<p class="abs video-text">Lorem ipsum dolor sit amet, consectetuer adipiscing elit. Aenean commodo ligula eget dolor. Aenean massa.Cum sociis natoque penatibus et magnis dis parturient montes, nascetur ridiculus mus. Donec quam felis, ultricies nec.</p>

<div class="abs news-item" style="top:770px">
  <div class="news-thumb" role="img" aria-label="Photo of a group of students" style="background:linear-gradient(135deg,#c9b79a,#7d8fa8)"></div>
  <div class="news-body"><h3>Lorem ipsum dolor sit amet, consectetuer adipiscing elit.</h3><div class="date">Posted On 21/11/2014</div><p>Aenean commodo ligula eget dolor. Aenean massa. Cum sociis natoque penatibus et magnis dis parturient montes.</p></div>
</div>
<div class="abs news-item" style="top:832px">
  <div class="news-thumb" role="img" aria-label="Photo of a student in front of a chalkboard" style="background:linear-gradient(90deg,#d8cfc4,#3b3f3c)"></div>
  <div class="news-body"><h3>Lorem ipsum dolor sit amet, consectetuer adipiscing elit.</h3><div class="date">Posted On 21/11/2014</div><p>Aenean commodo ligula eget dolor. Aenean massa. Cum sociis natoque penatibus et magnis dis parturient montes.</p></div>
</div>
<div class="abs news-item" style="top:895px">
  <div class="news-thumb" role="img" aria-label="Photo of students studying together" style="background:linear-gradient(135deg,#b8a58e,#e4ddd2)"></div>
  <div class="news-body"><h3>Lorem ipsum dolor sit amet, consectetuer adipiscing elit.</h3><div class="date">Posted On 21/11/2014</div><p>Aenean commodo ligula eget dolor. Aenean massa. Cum sociis natoque penatibus et magnis dis parturient montes.</p></div>
</div>

<footer class="abs footer">
  <div class="fcol" style="left:83px;width:118px">
    <h4>Contact Us</h4>
    <p>Fusce dapibus, tellus condimentum utellus fermalsuada magna. Fusce dapibus, tellus magna.</p>
    <div class="fcontact">
      <div><svg width="6" height="8" viewBox="0 0 6 8" style="flex:none;margin-top:2px"><path d="M3 0a3 3 0 013 3c0 2-3 5-3 5S0 5 0 3a3 3 0 013-3z" fill="#e6eaf2"/></svg><span>4120 Larchmont Road • PO Box 880 • Fernbrook • BC • CANADA • V0X 2K4</span></div>
      <div><svg width="6" height="6" viewBox="0 0 10 10" style="flex:none;margin-top:3px"><path d="M2 0l2 2.5-1 1.2c.6 1.4 1.8 2.6 3.2 3.2l1.2-1L10 8l-1.5 2C4 9.5.5 6 0 1.5z" fill="#e6eaf2"/></svg><span>(604) 555-0182</span></div>
      <div><svg width="7" height="5" viewBox="0 0 10 7" style="flex:none;margin-top:4px"><rect width="10" height="7" fill="#e6eaf2"/><path d="M0 0l5 4 5-4" stroke="#0e2248" fill="none"/></svg><span>info@cedarvaleridge.ca</span></div>
    </div>
  </div>
  <div class="divider" style="left:207px"></div>
  <div class="fcol" style="left:227px;width:140px">
    <h4>Latest Tweets</h4>
    <div class="tweet"><span class="dot"></span><span>Aenean lacinia bibendum nulla sed leo posuere erat a ante venenatis dapibus <span class="muted">posuere velit aliquet.</span></span></div>
    <div class="tweet"><span class="dot"></span><span>Donec ullamcorper metus auctor fringilla. Nullam <span class="muted">quis risus eget.</span></span></div>
    <div class="tweet"><span class="dot"></span><span><span class="muted">Vestibulum id ligula</span> porta euismod semper. Maecenas faucibus mollis.</span></div>
  </div>
  <div class="divider" style="left:382px"></div>
  <div class="fcol" style="left:401px;width:140px">
    <h4>Admissions</h4>
    <ul><li>Download the full Catalogue</li><li>Apply Today (Application Package)</li><li>Information Request</li><li>Browse our Programs</li><li>Download Forms</li><li>Admissions Information</li><li>Campus Directory</li></ul>
  </div>
  <div class="divider" style="left:538px"></div>
  <div class="fcol" style="left:566px;width:90px">
    <h4>Admissions</h4>
    <ul><li>Home</li><li>About Us</li><li>Consider Cedarvale</li><li>Current Students</li><li>Alumni</li><li>Supporters</li><li>News + Events</li></ul>
  </div>
  <div class="copyright"><span>© 2014 Copyright - cedarvaleridge - All Rights Reserved</span><span>Top &nbsp;⌃</span></div>
</footer>

</body>
</html>
```